New Business Card for Software Company

We are looking at rebranding a 10 year old company that specializes in PDF and DWF solutions for Architects and Engineers. We will attach the new company logo that we are going with so you can work with that and complimentary colors.
The sample information we would like on the business card is:
Gerald Pinfold
Vice President
4738 W. Harrowgate Lane. STE 305
PMB#417
Mesa, AZ 85374
866-392-5074 US Toll Free
123-456-3190 Cell
gpinfold@plavorix.com
The old tag line that we had on the business cars was.
Providing Industrial Strength PDF and DWF Solutions to the Global CAD Marketplace.
If you have an idea for a better tag line we are open to that also.
Updates
We would like to thank all of the Designers for their wonderful work. We apologize that we will not have the time to provide feedback to everyone. There is just so many innovative and professional designs that you have all created making our decision even harder.
Target Market(s)
Architects and Engineers
Industry/Entity Type
Business
Look and feel

```html
<!DOCTYPE html>
<html lang="en">
<head>
<meta charset="utf-8">
<title>Plavorix Business Card</title>
<link rel="stylesheet" href="https://fonts.googleapis.com/css2?family=Open+Sans:wght@400;600;700;800&display=swap">
<style>
  :root {
    --page: #ffffff;
    --card-front: #fbfbfb;
    --orange: #f05a24;
    --ink: #4a4a4a;
    --ink-soft: #5c5c5c;
    --rule: #c9c9c9;
    --band: #6b6b6b;
    --back-dark: #333333;
    --back-light: #a3a3a3;
    --white: #ffffff;
  }
  * { margin: 0; padding: 0; box-sizing: border-box; }
  html, body {
    width: 921px; height: 1200px; overflow: hidden;
    background: var(--page);
    font-family: "Open Sans", Arial, sans-serif;
  }
  .canvas { position: relative; width: 921px; height: 1200px; }

  .card {
    position: absolute; left: 64px; width: 794px; overflow: hidden;
    box-shadow: 0 2px 10px rgba(0,0,0,0.25);
  }
  .card-front { top: 107px; height: 454px; background: var(--card-front); }
  .card-back {
    top: 621px; height: 460px;
    background: linear-gradient(90deg, var(--back-dark) 0%, #6e6e6e 45%, var(--back-light) 100%);
  }

  .front-glow {
    position: absolute; right: -60px; top: -30px; width: 380px; height: 380px;
    border-radius: 50%; background: var(--orange); opacity: 0.06;
  }
  .brand { position: absolute; left: 49px; top: 50px; display: flex; align-items: center; gap: 12px; }
  .brand-dot { width: 54px; height: 54px; border-radius: 50%; background: var(--orange); }
  .brand-name { font-size: 46px; font-weight: 800; color: var(--ink); letter-spacing: -1px; }

  .name-tab { position: absolute; left: 23px; top: 193px; width: 16px; height: 67px; background: var(--band); }
  .name-ribbon { position: absolute; left: 39px; top: 193px; width: 706px; height: 67px; }
  .name-ribbon svg { position: absolute; inset: 0; }
  .person-name {
    position: absolute; left: 19px; top: 6px; color: var(--white);
    font-size: 27px; font-weight: 400; white-space: nowrap;
  }
  .person-name strong { font-weight: 700; }
  .person-title { position: absolute; left: 137px; top: 39px; color: var(--white); font-size: 18px; }

  .divider { position: absolute; left: 49px; top: 287px; width: 696px; height: 2px; background: var(--rule); }

  .contact { position: absolute; font-size: 18px; line-height: 26.5px; color: var(--ink-soft); }
  .contact b { font-weight: 700; color: var(--ink); }
  .contact-address { left: 49px; top: 304px; }
  .contact-email { left: 49px; top: 386px; }
  .contact-phones { left: 479px; top: 353px; }

  .footer-band { position: absolute; left: 0; bottom: 0; width: 100%; height: 34px; background: var(--band); }

  .back-glow {
    position: absolute; left: 20px; top: 80px; width: 360px; height: 360px;
    border-radius: 50%; background: var(--white); opacity: 0.07;
  }
  .back-brand {
    position: absolute; right: 64px; top: 190px;
    font-size: 76px; font-weight: 800; color: var(--white); letter-spacing: -2px; line-height: 1;
  }
  .back-square { position: absolute; right: 0; top: 196px; width: 28px; height: 64px; background: var(--orange); }
  .tagline {
    position: absolute; right: 53px; top: 343px; text-align: right;
    color: var(--white); font-size: 19px; line-height: 33px; letter-spacing: 0.8px;
  }
</style>
</head>
<body>
<div class="canvas">

  <section class="card card-front">
    <div class="front-glow"></div>
    <div class="brand">
      <span class="brand-dot"></span>
      <span class="brand-name">Plavorix</span>
    </div>

    <div class="name-tab"></div>
    <div class="name-ribbon">
      <svg width="706" height="67" viewBox="0 0 706 67" aria-hidden="true">
        <polygon points="0,0 706,0 682,33.5 706,67 0,67" fill="var(--orange)"/>
      </svg>
      <div class="person-name">Gerald <strong>Pinfold</strong></div>
      <div class="person-title">Vice President</div>
    </div>

    <div class="divider"></div>

    <div class="contact contact-address">
      <b>Address:</b> 4738 W. Harrowgate Lane. STE 305<br>
      PMB#417<br>
      Mesa, AZ 85374
    </div>
    <div class="contact contact-email"><b>Email:</b> gpinfold@plavorix.com</div>
    <div class="contact contact-phones">
      <b>US Toll Free:</b> 866-392-5074<br>
      <b>Cell:</b>123-456-3190
    </div>

    <div class="footer-band"></div>
  </section>

  <section class="card card-back">
    <div class="back-glow"></div>
    <div class="back-brand">Plavorix</div>
    <div class="back-square"></div>
    <p class="tagline">
      Providing Industrial Strength PDF and DWF<br>
      Solutions to the Global CAD Marketplace.
    </p>
  </section>

</div>
</body>
</html>
```